Profesional personal website needs design and business card

I need a business card with my professional name as a logo "Dorian Vitality" for my business. I am a Wellness Coach, consultant and trainer. So it should be professional, wellness oriented and modern.

Target Market(s)

Private clients, governments, corporations. Luxury and high market.

Industry/Entity Type

Health And Wellness

Contact Information for Business Card

Dorian Vitality should be the logo

Colors

Designer to choose colors to be used in the design.

Requirements
Must have
• Dorian Vitality
• Name: Tomás Lirandel
• Wellness Coach, Consultant & Trainer.
• Website: www.dorianvitality-example.com
• Phone:
• Spain (+34) 612 480 317
• (USA) +1 (555) 610 4829
Nice to have
• The most important is the design of "Dorian Vitality", as this is going to be my personal brand logo. It should be professional, wellness, high end and actual.
Should not have
• no golds, no baroque style..

```html
<!DOCTYPE html>
<html lang="en">
<head>
<meta charset="UTF-8">
<title>Dorian Vitality — Business Card</title>
<link rel="stylesheet" href="https://fonts.googleapis.com/css2?family=Montserrat:wght@400;500;700&display=swap">
<style>
  :root {
    --bg: #2a2a2b;
    --brand-blue: #1820a6;
    --brand-blue-deep: #0e1690;
    --accent-yellow: #f6b816;
    --white: #ffffff;
  }
  * { box-sizing: border-box; margin: 0; padding: 0; }
  html, body {
    width: 1200px; height: 930px; overflow: hidden;
    background: var(--bg);
    font-family: 'Montserrat', sans-serif;
  }
  .stage { position: relative; width: 1200px; height: 930px; }

  .card {
    position: absolute;
    width: 560px; height: 320px;
    border-radius: 22px;
    overflow: hidden;
    background: linear-gradient(135deg, var(--brand-blue) 0%, var(--brand-blue-deep) 100%);
    box-shadow: 0 18px 40px rgba(0,0,0,.45);
  }
  .card--front { left: 70px; top: 90px; }
  .card--back { left: 570px; top: 520px; }

  .wordmark {
    font-weight: 700;
    letter-spacing: 1px;
    text-transform: uppercase;
    white-space: nowrap;
  }
  .card--front .wordmark {
    position: absolute; left: 0; right: 0; top: 140px;
    text-align: center; color: var(--white); font-size: 34px;
  }

  .back-shape { position: absolute; inset: 0; }
  .card--back .wordmark {
    position: absolute; left: 330px; top: 124px;
    width: 220px; text-align: center;
    color: var(--brand-blue); font-size: 21px;
  }

  .person { position: absolute; left: 34px; top: 44px; color: var(--white); }
  .person__name { font-size: 20px; font-weight: 700; letter-spacing: .5px; white-space: nowrap; }
  .person__name .surname { color: var(--accent-yellow); }
  .person__role { font-size: 12px; font-weight: 500; line-height: 1.45; margin-top: 6px; padding-left: 14px; }

  .address {
    position: absolute; left: 58px; top: 168px;
    color: var(--white); font-size: 12px; font-weight: 500; line-height: 1.45;
  }
  .contacts {
    position: absolute; left: 40px; top: 218px;
    list-style: none; color: var(--white); font-size: 12px; font-weight: 500;
  }
  .contacts li { display: flex; align-items: center; gap: 8px; height: 19px; white-space: nowrap; }
  .contacts svg { width: 11px; height: 11px; flex: none; }
  .contacts .hl { color: var(--accent-yellow); }
</style>
</head>
<body>
<main class="stage">

  <section class="card card--front" aria-label="Card front">
    <div class="wordmark">Dorian Vitality</div>
  </section>

  <section class="card card--back" aria-label="Card back">
    <svg class="back-shape" viewBox="0 0 560 320" aria-hidden="true">
      <circle cx="440" cy="120" r="184" fill="var(--accent-yellow)"/>
      <circle cx="450" cy="118" r="180" fill="var(--white)"/>
    </svg>
    <div class="wordmark">Dorian Vitality</div>

    <div class="person">
      <div class="person__name">TOMÁS <span class="surname">LIRANDEL</span></div>
      <div class="person__role">Wellness Coach,<br>Consultant &amp; Trainer</div>
    </div>

    <div class="address">418 Brookmere Ave<br>Vernholt, BC, V2X 4K8</div>

    <ul class="contacts">
      <li>
        <svg viewBox="0 0 12 12"><path d="M2.5 1l2 2.2-1 1.3a6 6 0 0 0 4 4l1.3-1 2.2 2-1.2 1.5C5.5 11 1 6.5.9 2.3z" fill="var(--accent-yellow)"/></svg>
        (+34) 612 480 317
      </li>
      <li>
        <svg viewBox="0 0 12 12"><rect x="3" y=".8" width="6" height="10.4" rx="1.2" fill="none" stroke="var(--accent-yellow)" stroke-width="1.3"/></svg>
        +1 (555) 610 4829
      </li>
      <li>
        <svg viewBox="0 0 12 12"><rect x=".8" y="2.3" width="10.4" height="7.4" rx="1" fill="none" stroke="var(--accent-yellow)" stroke-width="1.2"/><path d="M1 3l5 3.6L11 3" fill="none" stroke="var(--accent-yellow)" stroke-width="1.2"/></svg>
        info@dorianvitality-example.com
      </li>
      <li>
        <svg viewBox="0 0 12 12"><circle cx="6" cy="6" r="5" fill="none" stroke="var(--accent-yellow)" stroke-width="1.2"/><path d="M1 6h10M6 1c-2.2 2.8-2.2 7.2 0 10M6 1c2.2 2.8 2.2 7.2 0 10" fill="none" stroke="var(--accent-yellow)" stroke-width="1"/></svg>
        <span>www.<span class="hl">dorianvitality-example</span>.com</span>
      </li>
    </ul>
  </section>

</main>
</body>
</html>
```